Computer Company needs a Business card design

We need a business card design for our business. We assist people to transition to the KVS (Kestrel Vantage Scheme). The Verandal Crown Office-owned kvs™ network is a brand new telecommunications network currently being rolled out across Australia, giving access to a reliable broadband connection. Our niche market will predominantly be domestic customers in the 50+ age bracket. The assistance that we provide is everything from arranging the equipment, arranging the plan and contract term, appointment times, final testing of the network and any tweaks that need to be made. We basically PM the transition from start to finish. The business card design should be minimalist, should communicate loyalty and stability, should be easy to read and clearly explain what we do. We have asked for front and back. However, the back of the card does not have to include much information at all. It could be just a small design, or a repeat of our phone number. Up to you. The attached file only says what is required on the card. It does not specify where to arrange the text, what fonts to use, etc etc. As much as we would like to give you more info, due to our very limited design ability, we are not really able to send you any rough, or otherwise, designs of what we are after. Hopefully the above description is enough for you.

```html
<!DOCTYPE html>
<html lang="en">
<head>
<meta charset="utf-8">
<title>Harbourline Connect – Business Card</title>
<link href="https://fonts.googleapis.com/css2?family=Open+Sans:ital,wght@0,400;0,700;1,400&display=swap" rel="stylesheet">
<style>
  :root {
    --backdrop: #58585a;
    --card: #ffffff;
    --ink-dark: #3b3b3d;
    --ink-mid: #6f6f71;
    --accent: #1a8fd6;
    --icon: #7a7a7c;
  }
  * { margin: 0; padding: 0; box-sizing: border-box; }
  html, body {
    width: 1037px;
    height: 1200px;
    overflow: hidden;
    background: var(--backdrop);
    font-family: "Open Sans", Arial, sans-serif;
  }
  .canvas {
    position: relative;
    width: 1037px;
    height: 1200px;
  }
  .card {
    position: absolute;
    left: 80px;
    width: 884px;
    height: 510px;
    background: var(--card);
    border-radius: 34px;
  }
  .card--front { top: 62px; }
  .card--back  { top: 614px; }

  .brand {
    position: absolute;
    left: 0;
    right: 0;
    display: flex;
    justify-content: center;
    align-items: center;
    gap: 14px;
  }
  .card--front .brand { top: 182px; }
  .card--back .brand  { top: 232px; }
  .brand__dot {
    width: 18px;
    height: 18px;
    border-radius: 50%;
    background: var(--accent);
  }
  .brand__name {
    font-size: 46px;
    font-weight: 700;
    color: var(--ink-dark);
    line-height: 1;
  }

  .tagline {
    position: absolute;
    top: 256px;
    left: 0;
    right: 0;
    text-align: center;
    font-style: italic;
    font-size: 26px;
    color: var(--ink-dark);
  }
  .holder {
    position: absolute;
    top: 344px;
    left: 0;
    right: 0;
    text-align: center;
    font-weight: 700;
    font-size: 27px;
    color: var(--ink-mid);
  }
  .contact {
    position: absolute;
    top: 414px;
    left: 0;
    right: 0;
    list-style: none;
    font-size: 21px;
    color: var(--ink-mid);
    line-height: 30px;
  }
  .contact__item {
    display: flex;
    justify-content: center;
    align-items: center;
    gap: 10px;
  }
  .contact__icon { width: 18px; height: 18px; }
</style>
</head>
<body>
<main class="canvas">
  <section class="card card--front" aria-label="Card front">
    <div class="brand">
      <span class="brand__dot"></span>
      <span class="brand__name">Harbourline Connect</span>
    </div>
    <p class="tagline">‘Your kvs move, handled every step of the way’</p>
    <p class="holder">Martin Ellery</p>
    <ul class="contact">
      <li class="contact__item">
        <svg class="contact__icon" viewBox="0 0 24 24" fill="none" stroke="var(--icon)" stroke-width="1.8" stroke-linejoin="round" aria-hidden="true">
          <path d="M5 3h4l2 5-2.5 1.5a11 11 0 0 0 6 6L16 13l5 2v4a2 2 0 0 1-2 2A16 16 0 0 1 3 5a2 2 0 0 1 2-2z"/>
        </svg>
        <span>0400 555 182</span>
      </li>
      <li class="contact__item">
        <svg class="contact__icon" viewBox="0 0 24 24" fill="none" stroke="var(--icon)" stroke-width="1.8" aria-hidden="true">
          <rect x="3" y="6" width="18" height="12"/>
          <path d="M3 6l9 7 9-7"/>
        </svg>
        <span>martin@harbourlineconnect.com.au</span>
      </li>
    </ul>
  </section>

  <section class="card card--back" aria-label="Card back">
    <div class="brand">
      <span class="brand__dot"></span>
      <span class="brand__name">Harbourline Connect</span>
    </div>
  </section>
</main>
</body>
</html>
```